Business Card Design

I need business cards designed for a new company i have started that makes cakes, particularly themed kids cakes with a really modern design and I would like to have my business cards reflect this. I have attached some photos of cakes I have made and would like some to be used.

Industry/Entity Type

Business

Contact Information for Business Card

Business Name: Tarts and Treats by Maren
Mobile: 0492 815 063
email: maren@tartsandtreatsbymaren.example.au
Instagram: instagram.com/tartsandtreatsbymaren/
Facebook: fb.me/tartsandtreatsbymaren

Colors
e667a6
b768aa
3276b5

Requirements
Must have
• Business Name: Tarts and Treats by Maren
• Mobile: 0492 815 063
• email: maren@tartsandtreatsbymaren.example.au
• Instagram: instagram.com/tartsandtreatsbymaren/
• Facebook: fb.me/tartsandtreatsbymaren
Nice to have
• 2 to 3 pictures of my cakes

```html
<!DOCTYPE html>
<html lang="en">
<head>
<meta charset="utf-8">
<title>Tarts and Treats by Maren – Business Card</title>
<link rel="stylesheet" href="https://fonts.googleapis.com/css2?family=Open+Sans:wght@300;400&display=swap">
<style>
  :root {
    --page-bg: #e9e4e1;
    --card-bg: #f5f2f3;
    --brand-pink: #e667a6;
    --brand-deep: #c2185b;
    --brand-plum: #b768aa;
    --brand-violet: #8e3c86;
    --brand-blue: #3276b5;
    --text-light: #ffffff;
    --text-soft: #fbe6f0;
  }
  * { box-sizing: border-box; margin: 0; padding: 0; }
  html, body {
    width: 1200px;
    height: 969px;
    overflow: hidden;
    background: var(--page-bg);
    font-family: "Open Sans", Arial, sans-serif;
  }
  .business-card {
    position: absolute;
    left: 100px;
    top: 199px;
    width: 1000px;
    height: 570px;
    background: var(--card-bg);
    border-radius: 6px;
    overflow: hidden;
    box-shadow: 0 10px 30px rgba(60, 30, 45, 0.18);
  }
  .card-swoosh {
    position: absolute;
    inset: 0;
    width: 1000px;
    height: 570px;
  }
  .brand-block {
    position: absolute;
    left: 70px;
    top: 78px;
    display: flex;
    align-items: center;
    gap: 26px;
  }
  .brand-dot {
    width: 120px;
    height: 120px;
    border-radius: 50%;
    background: var(--brand-plum);
    flex: none;
  }
  .brand-name {
    color: var(--brand-deep);
    font-weight: 400;
    line-height: 1.05;
  }
  .brand-name .line-main { display: block; font-size: 52px; letter-spacing: -0.5px; }
  .brand-name .line-by {
    display: block;
    margin-top: 10px;
    font-size: 20px;
    letter-spacing: 4px;
    text-transform: uppercase;
    padding-left: 120px;
  }
  .contact-block {
    position: absolute;
    right: 40px;
    top: 286px;
    text-align: right;
    color: var(--text-light);
  }
  .person-name {
    font-size: 32px;
    font-weight: 400;
    letter-spacing: 0.5px;
    text-transform: uppercase;
    padding-right: 44px;
  }
  .person-role {
    font-size: 25px;
    font-weight: 300;
    color: var(--text-soft);
    padding-right: 44px;
    margin-top: 2px;
  }
  .contact-list {
    list-style: none;
    margin-top: 22px;
  }
  .contact-list li {
    display: flex;
    justify-content: flex-end;
    align-items: center;
    gap: 18px;
    font-size: 23px;
    font-weight: 300;
    height: 38.5px;
  }
  .contact-icon {
    width: 24px;
    height: 24px;
    flex: none;
  }
  .social-mark {
    width: 20px;
    height: 20px;
    margin: 0 2px;
    background: var(--text-light);
    border-radius: 3px;
    flex: none;
  }
</style>
</head>
<body>
  <section class="business-card" aria-label="Tarts and Treats by Maren business card">
    <svg class="card-swoosh" viewBox="0 0 1000 570" aria-hidden="true">
      <defs>
        <linearGradient id="swooshFill" x1="0" y1="1" x2="1" y2="0">
          <stop offset="0" stop-color="#b8165a"/>
          <stop offset="0.55" stop-color="#c92a72"/>
          <stop offset="1" stop-color="#e667a6"/>
        </linearGradient>
      </defs>
      <path d="M0,540 C230,545 380,390 560,262 C720,150 860,160 1000,185 L1000,570 L0,570 Z" fill="url(#swooshFill)"/>
      <path d="M0,520 C240,525 380,360 560,240 C720,135 860,145 1000,168" fill="none" stroke="#8e3c86" stroke-width="5"/>
      <path d="M0,505 C250,510 390,340 575,222 C730,125 870,130 1000,150" fill="none" stroke="#b768aa" stroke-width="2"/>
    </svg>

    <div class="brand-block">
      <div class="brand-dot"></div>
      <div class="brand-name">
        <span class="line-main">Tarts &amp;</span>
        <span class="line-main">Treats</span>
        <span class="line-by">by Maren</span>
      </div>
    </div>

    <div class="contact-block">
      <p class="person-name">Jonah Pell</p>
      <p class="person-role">CEO/Founder</p>
      <ul class="contact-list">
        <li>0492 815 063
          <svg class="contact-icon" viewBox="0 0 24 24" aria-hidden="true">
            <rect x="6" y="1.5" width="12" height="21" rx="2" fill="none" stroke="#fff" stroke-width="1.8"/>
            <line x1="10" y1="19" x2="14" y2="19" stroke="#fff" stroke-width="1.8"/>
          </svg>
        </li>
        <li>maren@tartsandtreatsbymaren.example.au
          <svg class="contact-icon" viewBox="0 0 24 24" aria-hidden="true">
            <rect x="2" y="5" width="20" height="14" fill="#fff"/>
            <path d="M2,5 L12,13 L22,5" fill="none" stroke="#c92a72" stroke-width="1.6"/>
          </svg>
        </li>
        <li>tartsandtreatsbymaren <span class="social-mark"></span></li>
        <li>tartsandtreatsbymaren <span class="social-mark"></span></li>
      </ul>
    </div>
  </section>
</body>
</html>
```